Home Remodeling company needs a business card design

we need a business card design for home remodeling company in hamilton county, indiana USA. we offers a wide range of construction services including whole house renovations, Design and Build Basements and Kitchen and Bathroom Remodeling . we would like to see designs for both site of business card that use the same color of the company logo and also including all information below :
1- Karim Feltous CEO / General Contractor
2- all company contacts Telephone numbers ( 1-888-DULOM-47 ) ( 317-555-0193) email address ( info@dulomhome.com) website ( www.dulomhome.com ) and social media logos (Facebook- twitter- google plus )
3- company logo
4- licensed . insured . bonded

```html
<!DOCTYPE html>
<html lang="en">
<head>
<meta charset="utf-8">
<title>Dulom Business Card</title>
<link href="https://fonts.googleapis.com/css2?family=Cabin:wght@400;700&display=swap" rel="stylesheet">
<style>
  :root {
    --backdrop: #dedcd8;
    --card: #f0efed;
    --ink: #2a2a2a;
    --ink-soft: #3d3d3d;
    --brand-red: #8e1b1f;
    --panel: #161616;
    --chip: #d9d6cf;
  }
  * { margin: 0; padding: 0; box-sizing: border-box; }
  html, body { width: 1200px; height: 969px; overflow: hidden; }
  body {
    background: var(--backdrop);
    font-family: "Cabin", sans-serif;
    position: relative;
  }
  .card {
    position: absolute;
    left: 100px; top: 200px;
    width: 1000px; height: 568px;
    background: var(--card);
    box-shadow: 0 10px 30px rgba(0,0,0,.15);
    overflow: hidden;
  }
  .card-panel { position: absolute; inset: 0; }
  .company-name {
    position: absolute; left: 52px; top: 66px;
    font-weight: 700; font-size: 58px; line-height: 1;
    color: var(--ink);
  }
  .person { position: absolute; left: 52px; top: 198px; }
  .person-name { font-size: 35px; font-weight: 700; color: var(--ink); line-height: 1.2; }
  .person-role { font-size: 28px; color: var(--brand-red); margin-top: 4px; line-height: 1.2; }
  .contacts {
    position: absolute; left: 56px; top: 310px;
    list-style: none;
  }
  .contacts li {
    display: flex; align-items: center; gap: 22px;
    height: 39px; font-size: 26px; color: var(--ink-soft);
  }
  .contacts svg { width: 24px; height: 24px; fill: var(--brand-red); flex: none; }
  .credentials {
    position: absolute; left: 52px; top: 484px;
    font-size: 26px; color: var(--brand-red); letter-spacing: .5px;
  }
  .social {
    position: absolute; top: 472px; left: 812px;
    display: flex; gap: 8px;
  }
  .social span {
    width: 42px; height: 42px; border-radius: 50%;
    background: var(--chip);
  }
  .panel-square {
    position: absolute; left: 565px; top: 212px;
    width: 150px; height: 150px; background: var(--brand-red);
  }
</style>
</head>
<body>
  <div class="card">
    <svg class="card-panel" viewBox="0 0 1000 568" width="1000" height="568">
      <polygon points="525,0 1000,0 1000,568 525,568 955,284" fill="var(--panel)"/>
    </svg>

    <div class="panel-square"></div>

    <p class="company-name">DULOM</p>

    <div class="person">
      <p class="person-name">Karim Feltous</p>
      <p class="person-role">CEO / General Contractor</p>
    </div>

    <ul class="contacts">
      <li>
        <svg viewBox="0 0 24 24"><path d="M6.6 10.8a15 15 0 0 0 6.6 6.6l2.2-2.2c.3-.3.7-.4 1-.2 1.1.4 2.3.6 3.6.6.6 0 1 .4 1 1V20c0 .6-.4 1-1 1A17 17 0 0 1 3 4c0-.6.4-1 1-1h3.5c.6 0 1 .4 1 1 0 1.3.2 2.5.6 3.6.1.3 0 .7-.2 1z"/></svg>
        1-888-DULOM-47
      </li>
      <li>
        <svg viewBox="0 0 24 24"><path d="M7 1h10a2 2 0 0 1 2 2v18a2 2 0 0 1-2 2H7a2 2 0 0 1-2-2V3a2 2 0 0 1 2-2zm0 3v14h10V4zm5 15.5a1.2 1.2 0 1 0 0 2.4 1.2 1.2 0 0 0 0-2.4z"/></svg>
        317-555-0193
      </li>
      <li>
        <svg viewBox="0 0 24 24"><path d="M2 5h20v14H2zm2 2v.5l8 5 8-5V7zm0 2.8V17h16V9.8l-8 5z"/></svg>
        info@dulomhome.com
      </li>
      <li>
        <svg viewBox="0 0 24 24"><path d="M12 2a10 10 0 1 0 0 20 10 10 0 0 0 0-20zm-1 17.9A8 8 0 0 1 4.2 10L9 15v1a2 2 0 0 0 2 2zm6.9-2.5A2 2 0 0 0 16 16h-1v-3a1 1 0 0 0-1-1H8v-2h2a1 1 0 0 0 1-1V7h2a2 2 0 0 0 2-2v-.4a8 8 0 0 1 2.9 12.8z"/></svg>
        www.dulomhome.com
      </li>
    </ul>

    <p class="credentials">LICENSED | INSURED | BONDED</p>

    <div class="social">
      <span></span><span></span><span></span>
    </div>
  </div>
</body>
</html>
```